Vantro cards

I am in the auto motive, transportation business I would like a business card that is Something cool, modern edgy, having to do with car culture. I offer towing service for high and exotic cars. I also provide towing for collisions and car accidents. I offer open and enclosed transport nationwide.

Target Market(s)

Car culture people high end auto collectors

Industry/Entity Type

Towing car carrier

Contact Information for Business Card

My company colors black yellow and silver

Font styles to use
Serif

```html
<!DOCTYPE html>
<html lang="en">
<head>
<meta charset="utf-8">
<title>Vantro Transportation – Business Card</title>
<link rel="stylesheet" href="https://fonts.googleapis.com/css2?family=Arimo:wght@400;700&display=swap">
<style>
  :root {
    --page-bg: #3a3a3a;
    --card-black: #1f1f1f;
    --pattern-tone: #262626;
    --brand-yellow: #fce14a;
    --silver: #c9c9c9;
    --text-white: #f2f2f2;
  }
  * { margin: 0; padding: 0; box-sizing: border-box; }
  html, body {
    width: 1200px; height: 900px; overflow: hidden;
    background: var(--page-bg);
    font-family: "Arimo", Arial, sans-serif;
  }
  .canvas { position: relative; width: 1200px; height: 900px; }
  .card {
    position: absolute; left: 258px; width: 684px; height: 390px;
    background: var(--card-black); border-radius: 18px; overflow: hidden;
  }
  .card-front { top: 40px; }
  .card-back { top: 470px; }

  .front-brand {
    position: absolute; top: 78px; left: 0; right: 0; text-align: center;
  }
  .brand-name {
    display: inline-flex; align-items: center; gap: 12px;
    color: var(--brand-yellow); font-weight: 700; font-size: 44px; letter-spacing: 3px;
  }
  .brand-mark { width: 22px; height: 22px; background: var(--brand-yellow); }
  .brand-sub {
    margin-top: 6px; color: var(--silver); font-size: 14px; letter-spacing: 6px;
  }

  .front-details {
    position: absolute; top: 196px; left: 0; right: 0;
    display: flex; justify-content: center; align-items: stretch;
  }
  .person { text-align: right; padding: 14px 26px 0 0; }
  .person-name { color: var(--brand-yellow); font-weight: 700; font-size: 22px; letter-spacing: 1px; }
  .person-title { color: var(--text-white); font-size: 15px; margin-top: 4px; }
  .divider { width: 1.5px; background: var(--brand-yellow); }
  .contacts { list-style: none; padding-left: 24px; }
  .contacts li {
    display: flex; align-items: center; gap: 10px;
    color: var(--text-white); font-size: 14px; line-height: 24px;
  }
  .contacts svg { width: 14px; height: 14px; fill: var(--brand-yellow); flex: none; }

  .address {
    position: absolute; top: 318px; left: 0; right: 0; text-align: center;
    color: var(--text-white); font-size: 14px;
  }
  .front-stripe {
    position: absolute; left: 0; right: 0; bottom: 0; height: 10px;
    background: var(--brand-yellow);
  }

  .back-pattern {
    position: absolute; inset: 0;
    background: radial-gradient(circle at 50% 50%, var(--pattern-tone), var(--card-black));
  }
  .back-brand {
    position: absolute; top: 50%; left: 50%; transform: translate(-50%, -50%);
  }
  .back-brand .brand-name { font-size: 34px; }
</style>
</head>
<body>
<main class="canvas">
  <section class="card card-front">
    <div class="front-brand">
      <div class="brand-name"><span class="brand-mark"></span>VANTRO</div>
      <div class="brand-sub">TRANSPORTATION</div>
    </div>

    <div class="front-details">
      <div class="person">
        <div class="person-name">MARCUS HALE</div>
        <div class="person-title">CEO/Founder</div>
      </div>
      <div class="divider"></div>
      <ul class="contacts">
        <li>
          <svg viewBox="0 0 24 24" aria-hidden="true"><path d="M6.6 10.8a15.1 15.1 0 0 0 6.6 6.6l2.2-2.2a1 1 0 0 1 1-.25 11.4 11.4 0 0 0 3.6.57 1 1 0 0 1 1 1V20a1 1 0 0 1-1 1A17 17 0 0 1 3 4a1 1 0 0 1 1-1h3.5a1 1 0 0 1 1 1c0 1.25.2 2.45.57 3.6a1 1 0 0 1-.25 1z"/></svg>
          (555) 240 1187
        </li>
        <li>
          <svg viewBox="0 0 24 24" aria-hidden="true"><path d="M7 1h10a2 2 0 0 1 2 2v18a2 2 0 0 1-2 2H7a2 2 0 0 1-2-2V3a2 2 0 0 1 2-2zm0 3v14h10V4zm5 15.5a1 1 0 1 0 0 2 1 1 0 0 0 0-2z"/></svg>
          (555) 873 0462
        </li>
        <li>
          <svg viewBox="0 0 24 24" aria-hidden="true"><path d="M2 5h20v14H2zm2 2v.5l8 5 8-5V7zm0 2.8V17h16V9.8l-8 5z"/></svg>
          info@vantrotransportation.com
        </li>
        <li>
          <svg viewBox="0 0 24 24" aria-hidden="true"><path d="M12 2a10 10 0 1 0 0 20 10 10 0 0 0 0-20zm6.9 6h-3a15 15 0 0 0-1.3-4A8 8 0 0 1 18.9 8zM12 4c.8 1.1 1.5 2.5 1.9 4h-3.8c.4-1.5 1.1-2.9 1.9-4zM4.3 14a8 8 0 0 1 0-4h3.4a16 16 0 0 0 0 4zm.8 2h3a15 15 0 0 0 1.3 4A8 8 0 0 1 5.1 16zm3-8h-3a8 8 0 0 1 4.3-4A15 15 0 0 0 8.1 8zM12 20c-.8-1.1-1.5-2.5-1.9-4h3.8c-.4 1.5-1.1 2.9-1.9 4zm2.3-6H9.7a14 14 0 0 1 0-4h4.6a14 14 0 0 1 0 4zm.3 6a15 15 0 0 0 1.3-4h3a8 8 0 0 1-4.3 4zm1.7-6a16 16 0 0 0 0-4h3.4a8 8 0 0 1 0 4z"/></svg>
          www.vantrotransportation.com
        </li>
      </ul>
    </div>

    <p class="address">P.O. Box 3370 Harbor Road Westfield AB 6120</p>
    <div class="front-stripe"></div>
  </section>

  <section class="card card-back">
    <div class="back-pattern" role="img" aria-label="Tone-on-tone repeating brand pattern across the card back"></div>
    <div class="back-brand">
      <div class="brand-name"><span class="brand-mark"></span>VANTRO</div>
    </div>
  </section>
</main>
</body>
</html>
```